Binder design for a veterinary clinic

We are seeking a talented designer to create a standout design for ring binders specifically for our veterinary clinic. These binders will be used to organize materials from our Continuing Professional Development (CPD) projects for colleagues and interns. The design should be clean, professional, and align with our brand guidelines. To give you a better understanding of our branding, we’ve included the design of our vehicles as a reference. As additional reference, please visit www.tierpraxora.at

Target Market(s)

veterinarians

Industry/Entity Type

Veterinary

Font styles to use
Sans Serif

Colors
0054AA
0677BA
7BADD7
CADEEF
E8F1F8
FFC000
F8CF3A
FAE287
FDF2CF
FEFAEE

Requirements
Must have
• Our Logo an a clean design
Should not have
• to much images

```html
<!DOCTYPE html>
<html lang="de">
<head>
<meta charset="utf-8">
<title>Tierpraxora – Ordner Innenseite</title>
<link rel="stylesheet" href="https://fonts.googleapis.com/css2?family=Montserrat:wght@300;400;700&display=swap">
<style>
  :root {
    --page-bg: #e4e4e2;
    --cover-navy: #2f4259;
    --cover-navy-dark: #24354a;
    --insert-white: #f6f6f6;
    --brand-gold: #d49f1c;
    --brand-navy: #22324a;
    --hole-metal: #c9ccd0;
  }
  * { margin: 0; padding: 0; box-sizing: border-box; }
  html, body {
    width: 1200px;
    height: 900px;
    overflow: hidden;
    background: var(--page-bg);
    font-family: "Montserrat", sans-serif;
  }
  .binder-cover {
    position: absolute;
    left: 330px;
    top: 70px;
    width: 540px;
    height: 760px;
    background: var(--cover-navy);
    border-radius: 6px;
    box-shadow: inset -14px 0 0 var(--cover-navy-dark);
  }
  .cover-insert {
    position: absolute;
    left: 34px;
    top: 30px;
    width: 250px;
    height: 700px;
    background: var(--insert-white);
    overflow: hidden;
  }
  .insert-content {
    position: absolute;
    left: 50%;
    top: 50%;
    width: 700px;
    height: 250px;
    transform: translate(-50%, -50%) rotate(90deg);
    display: flex;
    flex-direction: column;
    align-items: center;
    justify-content: center;
    gap: 34px;
  }
  .welcome-heading {
    font-weight: 400;
    font-size: 34px;
    line-height: 1.1;
    color: var(--brand-gold);
    text-align: center;
    letter-spacing: 0.5px;
  }
  .clinic-name-block { text-align: center; }
  .clinic-name {
    font-weight: 700;
    font-size: 30px;
    color: var(--brand-navy);
    letter-spacing: -0.5px;
  }
  .clinic-tagline {
    margin-top: 4px;
    font-weight: 400;
    font-size: 17px;
    color: var(--brand-gold);
    letter-spacing: 0.6px;
  }
  .cover-holes {
    position: absolute;
    right: 60px;
    top: 0;
    width: 80px;
    height: 100%;
  }
</style>
</head>
<body>
  <div class="binder-cover">
    <div class="cover-insert">
      <div class="insert-content">
        <h1 class="welcome-heading">Herzlich<br>willkommen im</h1>
        <div class="clinic-name-block">
          <div class="clinic-name">Tierpraxora</div>
          <div class="clinic-tagline">Fachklinik für Kleintiere</div>
        </div>
      </div>
    </div>
    <svg class="cover-holes" viewBox="0 0 80 760" aria-hidden="true">
      <rect x="28" y="250" width="22" height="70" rx="11" fill="var(--hole-metal)"/>
      <rect x="28" y="420" width="22" height="70" rx="11" fill="var(--hole-metal)"/>
      <circle cx="39" cy="620" r="18" fill="var(--hole-metal)"/>
      <circle cx="39" cy="620" r="12" fill="var(--cover-navy-dark)"/>
    </svg>
  </div>
</body>
</html>
```